Web design for financial services

A modern web design of financial services (brokerage firm)
Req.s and technology tags :
- Very mobile friendly.
- One paged with some inner pages.
- Animated sticky header .
- Member login area for e-trade.
- Support RTL language.
- HTML & CSS.

The logo will be Home link
• MPTR :
WHO WE ARE
Content :
i) Board of Directors
ii) Mission Statement
iii) Corporate Values
iv) Regulations
• Financial Services :
WHAT WE DO
Content:
i) Electronic trading
ii) Trading desk
iii) Institutional
iv) Investors Education
• News
• Market Tools
• Forms---- opens new page
• Careers---- opens new page
• Contact Us----opens new page

The website is :
http://www.mptr-doha-example.com/

The logo need some changes to be more modern and impressively , but with keeping same structure .

Some related websites :
https://www.lv-bourse.example/

financial market

Financial Service

Coded - Design and coding required

2 page

• same fonts of http://www.kwdholdings.example/

• - Very mobile friendly.
• - One paged with some inner pages.
• - Animated sticky header .
• - Member login area for e-trade.
• - Support RTL language.
• - HTML & CSS.
• Slider , some Qatari theme,
• i like the video inside the home page
• ex :http://www.kwdholdings.example/

```html
<!DOCTYPE html>
<html lang="en">
<head>
<meta charset="utf-8">
<title>MPTR – Market News</title>
<link href="https://fonts.googleapis.com/css2?family=Open+Sans:wght@400;600;700;800&display=swap" rel="stylesheet">
<style>
:root{
  --brand:#8e1b1f;
  --brand-dark:#6d1417;
  --ink:#1a1a1a;
  --body:#333333;
  --muted:#9a9a9a;
  --white:#ffffff;
  --footer:#000000;
  --rule:#e3e3e3;
}
*{box-sizing:border-box;margin:0;padding:0}
html,body{width:1200px;height:2242px;overflow:hidden;background:var(--white)}
body{font-family:"Open Sans",Arial,sans-serif;color:var(--ink);position:relative}

/* Header */
.site-header{position:absolute;top:0;left:0;width:1200px;height:120px;background:var(--white);z-index:3}
.brand{position:absolute;left:76px;top:40px;display:flex;align-items:center;gap:12px;text-decoration:none}
.brand-mark{width:38px;height:38px;border-radius:50%;background:var(--brand)}
.brand-name{font-weight:800;font-size:36px;color:var(--ink);letter-spacing:-0.5px}
.etrade-btn{position:absolute;left:926px;top:27px;width:102px;height:25px;background:var(--brand);color:var(--white);font-size:10px;font-weight:700;display:flex;align-items:center;justify-content:center;border-radius:2px;gap:5px}
.etrade-btn .icon{width:9px;height:10px;border:1.5px solid var(--white);border-radius:1px}
.lang-select{position:absolute;left:1037px;top:27px;width:87px;height:25px;border:1px solid #555;border-radius:2px;font-size:9px;font-weight:600;display:flex;align-items:center;justify-content:center;gap:5px;color:var(--ink)}
.lang-select .flag{width:12px;height:8px;background:linear-gradient(#2b3a8c,#c8202f)}
.lang-select .caret{width:5px;height:5px;border-right:1.5px solid #333;border-bottom:1.5px solid #333;transform:rotate(45deg);margin-top:-3px}
.main-nav{position:absolute;top:82px;right:76px;display:flex;gap:31px;font-size:12px;font-weight:700;text-transform:uppercase}
.main-nav a{color:var(--ink);text-decoration:none}
.main-nav a.is-active{color:var(--brand)}

/* Hero */
.hero{position:absolute;top:120px;left:0;width:1200px;height:545px;overflow:hidden}
.hero-photo{position:absolute;inset:0;background:linear-gradient(115deg,#2a2724 0%,#4a3d33 35%,#6a5a4c 55%,#3a322c 80%,#24201d 100%)}
.hero-shade{position:absolute;inset:0;background:rgba(0,0,0,0.25)}
.hero-cut{position:absolute;left:0;top:0;width:1200px;height:545px}
.hero-title{position:absolute;top:182px;left:0;width:100%;text-align:center;color:var(--white);font-size:60px;font-weight:700;letter-spacing:0.5px}

/* News */
.news{position:absolute;top:680px;left:160px;width:880px}
.news-heading{font-size:26px;font-weight:800;color:var(--ink);margin-top:2px}
.news-grid{position:absolute;top:76px;left:1px;display:grid;grid-template-columns:repeat(3,266px);column-gap:39px;row-gap:0}
.news-card{height:420px}
.news-card .thumb{width:266px;height:172px}
.news-card h3{margin-top:14px;font-size:16.5px;font-weight:600;line-height:26px;color:var(--ink)}
.news-card p{margin-top:10px;font-size:10.5px;line-height:20px;color:var(--body)}
.news-card time{display:block;margin-top:16px;font-size:14.5px;font-weight:700;color:var(--ink)}

.thumb-1{background:linear-gradient(180deg,#c9cdd2 0%,#9aa8b3 40%,#6e7f8a 60%,#c1b7a8 100%)}
.thumb-2{background:linear-gradient(180deg,#5a86b8 0%,#3d5f86 55%,#9db4c8 100%)}
.thumb-3{background:linear-gradient(180deg,#6d8fb3 0%,#e7c48c 40%,#5f9ca2 65%,#8c8576 100%)}
.thumb-4{background:linear-gradient(180deg,#e9ebee 0%,#d5d8dc 55%,#a9acb1 100%)}
.thumb-5{background:linear-gradient(135deg,#e6e9ee 0%,#b9c8dc 45%,#d9cfc0 100%)}
.thumb-6{background:linear-gradient(180deg,#cfd6d9 0%,#b9b1a6 50%,#8f8278 100%)}

/* Skyline band */
.skyline{position:absolute;top:1661px;left:0;width:1200px;height:326px;background:linear-gradient(180deg,rgba(255,255,255,0) 0%,#e3b6b0 30%,#b26a66 70%,#8e3a37 100%)}

/* Footer */
.site-footer{position:absolute;top:1987px;left:0;width:1200px;height:255px;background:var(--footer);color:var(--white);text-align:center}
.footer-brand{position:absolute;top:48px;left:0;width:100%;display:flex;justify-content:center;align-items:center;gap:10px}
.footer-brand .brand-mark{width:30px;height:30px;border-radius:50%;background:var(--white)}
.footer-brand .brand-name{color:var(--white);font-size:28px}
.footer-nav{position:absolute;top:126px;left:0;width:100%;font-size:13px;font-weight:700;display:flex;justify-content:center;gap:14px}
.footer-nav span.sep{font-weight:400}
.legal{position:absolute;top:158px;left:0;width:100%;font-size:10px;color:#cfcfcf}
.social{position:absolute;top:190px;left:0;width:100%;display:flex;justify-content:center;gap:5px}
.social span{width:28px;height:28px;border:1.5px solid var(--white);border-radius:50%;display:block}
</style>
</head>
<body>

<header class="site-header">
  <a class="brand" href="http://www.mptr-doha-example.com/">
    <span class="brand-mark"></span>
    <span class="brand-name">MPTR</span>
  </a>
  <div class="etrade-btn"><span class="icon"></span>MPTR E-TRADE</div>
  <div class="lang-select"><span class="flag"></span>ENGLISH<span class="caret"></span></div>
  <nav class="main-nav">
    <a href="#">MPTR</a>
    <a href="#">Financial Service</a>
    <a href="#" class="is-active">News</a>
    <a href="#">Market Tool</a>
    <a href="#">Forms</a>
    <a href="#">Careers</a>
    <a href="#">Contact Us</a>
  </nav>
</header>

<section class="hero">
  <div class="hero-photo" role="img" aria-label="Dimmed photo of hands reviewing financial charts beside a laptop"></div>
  <div class="hero-shade"></div>
  <h1 class="hero-title">MARKET NEWS</h1>
  <svg class="hero-cut" viewBox="0 0 1200 545" aria-hidden="true">
    <polygon points="0,473 374,401 1200,545 0,545" fill="#ffffff"/>
  </svg>
</section>

<main class="news">
  <h2 class="news-heading">NEWS</h2>
  <div class="news-grid">
    <article class="news-card">
      <div class="thumb thumb-1" role="img" aria-label="Photo of a family on a waterfront promenade facing a city skyline"></div>
      <h3>Sed ut perspiciloatis unde omnisste natusrror sit voluptat accusum.</h3>
      <p>Sed ut perspiciatis unde omnis iste natus err orspt atem accusantium dolore mque laudlorantiumam rem aperiam, eaque ipsa quae ab illo inventoreaet quasi arc hite cto beatae vitae dictasn.</p>
      <time>----- 25 January, 2017</time>
    </article>
    <article class="news-card">
      <div class="thumb thumb-2" role="img" aria-label="Photo of modern glass towers against a blue sky"></div>
      <h3>Sed ut perspiciloatis unde nis iste natusrror sit voluptat accusum.</h3>
      <p>Sed ut perspiciatis unde omnis iste natus err orspt atem accusantium dolore mque laudlorantiumam rem aperiam, eaque ipsa quae ab illo inventoreaet quasi arc hite cto beatae vitae dictasn.</p>
      <time>----- 25 January, 2017</time>
    </article>
    <article class="news-card">
      <div class="thumb thumb-3" role="img" aria-label="Photo of traditional boats in a bay at sunset"></div>
      <h3>Sed ut perspiciloa unde omnis iste natusrror sit voluptat accusum.</h3>
      <p>Sed ut perspiciatis unde omnis iste natus err orspt atem accusantium dolore mque laudlorantiumam rem aperiam, eaque ipsa quae ab illo inventoreaet quasi arc hite cto beatae vitae dictasn.</p>
      <time>----- 25 January, 2017</time>
    </article>
    <article class="news-card">
      <div class="thumb thumb-4" role="img" aria-label="Photo of a business meeting around a presentation board"></div>
      <h3>Sed ut perspiciloatis unde omnisste natusrror sit voluptat accusum.</h3>
      <p>Sed ut perspiciatis unde omnis iste natus err orspt atem accusantium dolore mque laudlorantiumam rem aperiam, eaque ipsa quae ab illo inventoreaet quasi arc hite cto beatae vitae dictasn.</p>
      <time>----- 25 January, 2017</time>
    </article>
    <article class="news-card">
      <div class="thumb thumb-5" role="img" aria-label="Photo of a phone showing charts on printed reports beside a coffee cup"></div>
      <h3>Sed ut perspiciloatis unde nis iste natusrror sit voluptat accusum.</h3>
      <p>Sed ut perspiciatis unde omnis iste natus err orspt atem accusantium dolore mque laudlorantiumam rem aperiam, eaque ipsa quae ab illo inventoreaet quasi arc hite cto beatae vitae dictasn.</p>
      <time>----- 25 January, 2017</time>
    </article>
    <article class="news-card">
      <div class="thumb thumb-6" role="img" aria-label="Photo of two colleagues discussing a tablet at a café table"></div>
      <h3>Sed ut perspiciloa unde omnis iste natusrror sit voluptat accusum.</h3>
      <p>Sed ut perspiciatis unde omnis iste natus err orspt atem accusantium dolore mque laudlorantiumam rem aperiam, eaque ipsa quae ab illo inventoreaet quasi arc hite cto beatae vitae dictasn.</p>
      <time>----- 25 January, 2017</time>
    </article>
  </div>
</main>

<div class="skyline" role="img" aria-label="Illustrated maroon skyline of city towers"></div>

<footer class="site-footer">
  <div class="footer-brand">
    <span class="brand-mark"></span>
    <span class="brand-name">MPTR</span>
  </div>
  <nav class="footer-nav">
    <span>MPTR</span><span class="sep">|</span>
    <span>FINACIAL SERVICE</span><span class="sep">|</span>
    <span>NEWS</span><span class="sep">|</span>
    <span>MARKET TOOL</span><span class="sep">|</span>
    <span>CAREERS</span><span class="sep">|</span>
    <span>CONTACT US</span>
  </nav>
  <p class="legal">©2017. All Rights Reserved | MPTR Qatar | Copyright, Legal and Privacy Statement.Disclaimers and Legal Information</p>
  <div class="social">
    <span></span><span></span><span></span><span></span><span></span>
  </div>
</footer>

</body>
</html>
```